Harborline Auto LLC

Car Dealer Customer Service
Address: 2874 Cresthaven Road, Shelbyville, TN 37162
web: www.harborlineautoxq.net
email: harborlineautoxq@mailnest.example
Phone: (931) 555-0148
Phone: (629) 555-0173

```html
<!DOCTYPE html>
<html lang="en">
<head>
<meta charset="utf-8">
<title>Harborline Auto LLC – Business Card</title>
<link rel="stylesheet" href="https://fonts.googleapis.com/css2?family=Open+Sans:wght@400;600;700&display=swap">
<style>
  :root {
    --stage: #3a3a3a;
    --card-white: #ffffff;
    --card-black: #141414;
    --brand-blue: #1f72b0;
    --accent-gold: #f0a830;
    --text-gray: #4a4a4a;
    --emboss: #2a2a2a;
    --emboss-light: #9a9a9a;
  }
  * { box-sizing: border-box; margin: 0; padding: 0; }
  html, body { width: 1200px; height: 801px; overflow: hidden; }
  body {
    background: var(--stage);
    font-family: "Open Sans", Arial, sans-serif;
    display: flex;
    align-items: center;
    justify-content: center;
    gap: 40px;
  }
  .card {
    width: 540px;
    height: 308px;
    position: relative;
    border-bottom: 3px solid var(--brand-blue);
    overflow: hidden;
  }
  .card--front { background: var(--card-white); display: flex; align-items: center; }
  .card--back { background: var(--card-black); display: flex; align-items: center; justify-content: center; }

  .brand {
    flex: 0 0 264px;
    padding: 0 18px;
    display: flex;
    flex-direction: column;
    align-items: center;
    gap: 14px;
  }
  .brand__dot { width: 84px; height: 84px; border-radius: 50%; background: var(--brand-blue); }
  .brand__name {
    font-weight: 700;
    font-size: 21px;
    letter-spacing: 0.5px;
    color: var(--brand-blue);
    text-transform: uppercase;
    white-space: nowrap;
  }
  .card--back .brand { flex: none; }
  .card--back .brand__dot { background: var(--emboss); width: 110px; height: 110px; }
  .card--back .brand__name { color: var(--emboss-light); font-size: 34px; }

  .divider { flex: none; width: 1px; height: 150px; background: var(--brand-blue); }

  .details { padding-left: 20px; padding-right: 12px; color: var(--text-gray); font-size: 12px; line-height: 1.5; white-space: nowrap; }
  .details__title { color: var(--brand-blue); font-weight: 700; font-size: 14px; margin-bottom: 2px; }
  .details__address { margin-bottom: 8px; }
  .contact { list-style: none; }
  .contact li { display: flex; align-items: center; gap: 7px; }
  .contact svg { width: 10px; height: 10px; flex: none; fill: var(--accent-gold); }
</style>
</head>
<body>
  <section class="card card--front" aria-label="Card front">
    <div class="brand">
      <span class="brand__dot"></span>
      <span class="brand__name">Harborline Auto</span>
    </div>
    <span class="divider"></span>
    <div class="details">
      <p class="details__title">Car Dealer Customer Service</p>
      <p class="details__address">2874 Cresthaven Road<br>Shelbyville, TN 37162</p>
      <ul class="contact">
        <li><svg viewBox="0 0 24 24"><path d="M6.6 10.8a15 15 0 0 0 6.6 6.6l2.2-2.2c.3-.3.7-.4 1-.2 1.1.4 2.3.6 3.6.6.6 0 1 .4 1 1V20c0 .6-.4 1-1 1A17 17 0 0 1 3 4c0-.6.4-1 1-1h3.5c.6 0 1 .4 1 1 0 1.3.2 2.5.6 3.6.1.3 0 .7-.2 1z"/></svg>(931) 555-0148</li>
        <li><svg viewBox="0 0 24 24"><path d="M6.6 10.8a15 15 0 0 0 6.6 6.6l2.2-2.2c.3-.3.7-.4 1-.2 1.1.4 2.3.6 3.6.6.6 0 1 .4 1 1V20c0 .6-.4 1-1 1A17 17 0 0 1 3 4c0-.6.4-1 1-1h3.5c.6 0 1 .4 1 1 0 1.3.2 2.5.6 3.6.1.3 0 .7-.2 1z"/></svg>(629) 555-0173</li>
        <li><svg viewBox="0 0 24 24"><path d="M2 5h20v14H2zm2 2v.5l8 5 8-5V7z"/></svg>harborlineautoxq@mailnest.example</li>
        <li><svg viewBox="0 0 24 24"><path d="M12 2a10 10 0 1 0 0 20 10 10 0 0 0 0-20zm6.9 9h-3a15 15 0 0 0-1.3-6A8 8 0 0 1 18.9 11zM12 4c1 1.4 1.8 4 1.9 7h-3.8C10.2 8 11 5.4 12 4zM9.4 5a15 15 0 0 0-1.3 6h-3A8 8 0 0 1 9.4 5zM5.1 13h3a15 15 0 0 0 1.3 6A8 8 0 0 1 5.1 13zM12 20c-1-1.4-1.8-4-1.9-7h3.8c-.1 3-.9 5.6-1.9 7zm2.6-1a15 15 0 0 0 1.3-6h3a8 8 0 0 1-4.3 6z"/></svg>www.harborlineautoxq.net</li>
      </ul>
    </div>
  </section>

  <section class="card card--back" aria-label="Card back">
    <div class="brand">
      <span class="brand__dot"></span>
      <span class="brand__name">Harborline Auto</span>
    </div>
  </section>
</body>
</html>
```